BOLD & MINIMALIST DESIGN NEEDED

We want a very bold but minimalistic business card design that is impactful and utilizes both sides of the business card. Our current logo is included for your use.

We want bold fonts and good use of negative space. We don't want the logo to overpower the design.

Target Market(s)

Professionals who are building new commercial buildings.

Industry/Entity Type

Construction

Contact Information for Business Card

Name, Title, email, office phone, cell phone, website

Font styles to use
Serif
Sans Serif

Requirements
Must have
• Bold design!

```html
<!DOCTYPE html>
<html lang="en">
<head>
<meta charset="utf-8">
<title>Ridgeline Design + Build — Business Card</title>
<link href="https://fonts.googleapis.com/css2?family=Montserrat:wght@400;500;800&display=swap" rel="stylesheet">
<style>
  :root {
    --backdrop: #b9b9b9;
    --card-dark: #1e1e1e;
    --card-light: #ffffff;
    --brand-green: #7cc242;
    --brand-green-soft: #b6e08e;
    --ink: #1a1a1a;
    --text-light: #ffffff;
  }
  * { margin: 0; padding: 0; box-sizing: border-box; }
  html, body {
    width: 1200px; height: 802px; overflow: hidden;
    background: var(--backdrop);
    font-family: "Montserrat", sans-serif;
  }
  .stage {
    width: 1200px; height: 802px;
    display: flex; align-items: center; justify-content: center; gap: 40px;
  }
  .card {
    position: relative;
    width: 540px; height: 309px;
    border-radius: 22px;
    overflow: hidden;
    background: var(--card-dark);
    box-shadow: 0 14px 30px rgba(0,0,0,0.28);
  }
  .card__curve { position: absolute; inset: 0; width: 100%; height: 100%; }

  .wordmark {
    position: absolute;
    display: flex; align-items: center; gap: 10px;
  }
  .wordmark__square {
    width: 20px; height: 20px; background: var(--brand-green);
  }
  .wordmark__text {
    font-weight: 800; letter-spacing: 0.02em; line-height: 1;
    text-transform: uppercase;
  }
  .card--front .wordmark { top: 30px; right: 48px; }
  .card--front .wordmark__text { font-size: 24px; color: var(--ink); }
  .card--back .wordmark { top: 50%; left: 50%; transform: translate(-50%, -50%); }
  .card--back .wordmark__text { font-size: 44px; color: var(--text-light); }

  .contact {
    position: absolute; left: 34px; bottom: 22px;
    color: var(--text-light);
  }
  .contact__name {
    font-weight: 800; font-size: 21px; line-height: 1.2; color: var(--brand-green);
    text-transform: uppercase; letter-spacing: 0.02em;
  }
  .contact__title { font-size: 13px; font-weight: 500; line-height: 1.3; margin-bottom: 10px; }
  .contact__list { list-style: none; }
  .contact__item {
    display: flex; align-items: center; gap: 9px;
    font-size: 12.5px; line-height: 1.65;
  }
  .contact__icon { width: 11px; height: 11px; flex: none; }
  .contact__accent { color: var(--brand-green); }
</style>
</head>
<body>
<main class="stage">

  <section class="card card--front" aria-label="Card front">
    <svg class="card__curve" viewBox="0 0 540 309" preserveAspectRatio="none" aria-hidden="true">
      <path d="M0,0 H540 V70 Q300,160 0,115 Z" fill="var(--card-light)"/>
      <path d="M0,115 Q300,160 540,70" fill="none" stroke="var(--brand-green)" stroke-width="6"/>
      <path d="M0,121 Q300,166 540,76" fill="none" stroke="var(--brand-green-soft)" stroke-width="2"/>
    </svg>

    <div class="wordmark">
      <span class="wordmark__square"></span>
      <span class="wordmark__text">Ridgeline Design + Build</span>
    </div>

    <div class="contact">
      <p class="contact__name">Daniel Marsh</p>
      <p class="contact__title">CEO/Founder</p>
      <ul class="contact__list">
        <li class="contact__item">
          <svg class="contact__icon" viewBox="0 0 12 12" aria-hidden="true"><path d="M2.5 1 L4.5 1 L5.5 3.5 L4 4.5 Q5 7 7.5 8 L8.5 6.5 L11 7.5 L11 9.5 Q10 11 8 11 Q1 9 1 3 Q1 1.5 2.5 1 Z" fill="var(--brand-green)"/></svg>
          07 5123 4400
        </li>
        <li class="contact__item">
          <svg class="contact__icon" viewBox="0 0 12 12" aria-hidden="true"><rect x="3" y="0.5" width="6" height="11" rx="1.2" fill="none" stroke="var(--brand-green)" stroke-width="1.3"/><circle cx="6" cy="9.5" r="0.8" fill="var(--brand-green)"/></svg>
          0412 555 019
        </li>
        <li class="contact__item">
          <svg class="contact__icon" viewBox="0 0 12 12" aria-hidden="true"><rect x="0.5" y="2" width="11" height="8" fill="var(--brand-green)"/><path d="M0.5 2 L6 6.5 L11.5 2" fill="none" stroke="var(--card-dark)" stroke-width="1"/></svg>
          info@ridgelinebuild.com
        </li>
        <li class="contact__item">
          <svg class="contact__icon" viewBox="0 0 12 12" aria-hidden="true"><circle cx="6" cy="6" r="5.3" fill="none" stroke="var(--brand-green)" stroke-width="1.3"/><path d="M0.7 6 H11.3 M6 0.7 Q2.5 6 6 11.3 M6 0.7 Q9.5 6 6 11.3" fill="none" stroke="var(--brand-green)" stroke-width="1"/></svg>
          <span>www.<span class="contact__accent">ridgelinebuild</span>.com</span>
        </li>
      </ul>
    </div>
  </section>

  <section class="card card--back" aria-label="Card back">
    <div class="wordmark">
      <span class="wordmark__square"></span>
      <span class="wordmark__text">Ridgeline</span>
    </div>
  </section>

</main>
</body>
</html>
```